Digital Billboard Design: Winter Sales Event

I own a boutique furniture store in Calgary, AB (larkhollowhome.ca) and I am looking to advertise our winter sale event on a new curved digital billboard (specs attached including required file type).

I have this billboard rented for 52-weeks so I will be looking to change the design every 4-weeks (i.e. this is intended to be an ongoing project).

The objective of this first billboard is to raise awareness around our annual winter sales event. The store itself is only a few blocks from the billboard so those commuting into downtown are just a short drive from the store.

I am looking for a fresh, clean, contemporary look that will grab your attention as you drive into downtown Calgary without presenting to much info so as to be distracting (and overwhelming -- the billboard does not need to contain all info on my current marketing material). I should also note that the store caters to a higher-end, more sophisticated clientele so the graphics need to reflect the brand (i.e. we are not Brenton Furniture or Couch Depot!).

I have attached three files:

Billboard specs
Current marketing material advertising sale (and all relevant data)
An idea that is from an American furniture store that I think is interesting

Target Market(s)

Upper middle class, sophisticated client who appreciates the finer things in life.

Industry/Entity Type

Furniture Store

Font styles to use
Sans Serif

Requirements
Must have
• Company Logo
• Winter Sales Event - 20 to 60% off
• Address: 2417 14th Ave SW
Nice to have
• Image of furniture -- see our website www.larkhollowhome.ca -- any photo from this site can be used
Should not have
• Too much text or visual distration

```html
<!DOCTYPE html>
<html lang="en">
<head>
<meta charset="utf-8">
<title>Lark Hollow Home — Winter Sales Event Billboard</title>
<link rel="stylesheet" href="https://fonts.googleapis.com/css2?family=Montserrat:wght@300;400;500&display=swap">
<style>
  :root {
    --page: #ffffff;
    --frame: #333333;
    --ink: #ffffff;
    --slate: #5f7878;
    --slate-light: #7a9090;
    --moss: #6c7558;
    --deep: #445654;
    --teal: #5c7f88;
    --sofa-tone: rgba(255, 255, 255, 0.10);
  }
  * { box-sizing: border-box; margin: 0; padding: 0; }
  html, body { width: 1200px; height: 1000px; overflow: hidden; background: var(--page); }
  body { position: relative; font-family: "Montserrat", Arial, sans-serif; color: var(--ink); }

  .presentation-frame {
    position: absolute; left: 34px; top: 36px; width: 1135px; height: 935px;
    border: 3px solid var(--frame);
  }

  .billboard {
    position: absolute; overflow: hidden;
    background:
      radial-gradient(circle at 30% 35%, rgba(150,170,175,0.35) 0, transparent 22%),
      radial-gradient(circle at 55% 80%, rgba(110,140,160,0.45) 0, transparent 18%),
      radial-gradient(ellipse at 10% 60%, var(--moss) 0, transparent 40%),
      radial-gradient(ellipse at 85% 70%, var(--teal) 0, transparent 45%),
      radial-gradient(ellipse at 20% 100%, var(--deep) 0, transparent 45%),
      linear-gradient(135deg, var(--slate) 0%, var(--slate-light) 50%, var(--slate) 100%);
  }
  .billboard--wide { left: 162px; top: 85px; width: 874px; height: 406px; }
  .billboard--feature { left: 164px; top: 516px; width: 873px; height: 404px; }

  .billboard > * { position: absolute; line-height: 1; white-space: nowrap; text-align: center; }

  .brand-name { font-weight: 300; letter-spacing: 6px; text-transform: uppercase; }
  .brand-address { font-weight: 300; text-transform: uppercase; }

  .event-title, .event-main, .offer-lead, .offer-amount, .offer-tail, .sale-end { width: 500px; }
  .event-title { font-weight: 300; font-size: 44px; }
  .event-title strong { font-weight: 400; }
  .event-main { font-weight: 300; font-size: 96px; }
  .offer-lead, .offer-tail { font-weight: 300; font-size: 52px; }
  .offer-amount { font-weight: 400; font-size: 88px; }
  .sale-end { font-weight: 300; font-size: 31px; }
  .sale-end strong { font-weight: 500; }

  .divider { width: 2px; background: var(--ink); opacity: 0.9; }

  /* wide layout */
  .billboard--wide .brand-name { left: 0; width: 100%; top: 30px; font-size: 33px; }
  .billboard--wide .brand-address { left: 0; width: 100%; top: 72px; font-size: 26px; }
  .billboard--wide .event-title { left: -29px; top: 158px; }
  .billboard--wide .event-main { left: -29px; top: 195px; }
  .billboard--wide .divider { left: 432px; top: 135px; height: 182px; }
  .billboard--wide .offer-lead { left: 393px; top: 131px; }
  .billboard--wide .offer-amount { left: 393px; top: 180px; }
  .billboard--wide .offer-tail { left: 393px; top: 268px; }
  .billboard--wide .sale-end { left: 187px; top: 347px; }

  /* feature layout */
  .billboard--feature .brand-name { left: 369px; width: 500px; top: 31px; font-size: 31px; }
  .billboard--feature .brand-address { left: 369px; width: 500px; top: 75px; font-size: 21px; }
  .furniture-image { left: 66px; top: 40px; width: 307px; height: 141px; background: var(--sofa-tone); border-radius: 60px 60px 6px 6px; }
  .billboard--feature .event-title { left: -31px; top: 197px; }
  .billboard--feature .event-main { left: -31px; top: 236px; }
  .billboard--feature .sale-end { left: -31px; top: 334px; }
  .billboard--feature .divider { left: 435px; top: 172px; height: 180px; }
  .billboard--feature .offer-lead { left: 397px; top: 168px; }
  .billboard--feature .offer-amount { left: 397px; top: 227px; }
  .billboard--feature .offer-tail { left: 397px; top: 304px; }
</style>
</head>
<body>
  <div class="presentation-frame"></div>

  <section class="billboard billboard--wide" aria-label="Winter sales event billboard, wide layout">
    <p class="brand-name">Lark Hollow Home</p>
    <p class="brand-address">2417 14th Ave SW, Calgary, AB</p>
    <p class="event-title">WINTER <strong>SALES</strong></p>
    <p class="event-main">EVENT</p>
    <div class="divider"></div>
    <p class="offer-lead">GET</p>
    <p class="offer-amount">20-60%</p>
    <p class="offer-tail">OFF</p>
    <p class="sale-end">SALE ENDS <strong>JANUARY 31ST</strong></p>
  </section>

  <section class="billboard billboard--feature" aria-label="Winter sales event billboard, layout with furniture">
    <p class="brand-name">Lark Hollow Home</p>
    <p class="brand-address">2417 14th Ave SW, Calgary, AB</p>
    <div class="furniture-image" role="img" aria-label="White line drawing of a sofa"></div>
    <p class="event-title">WINTER <strong>SALES</strong></p>
    <p class="event-main">EVENT</p>
    <p class="sale-end">ENDS <strong>JANUARY 31ST</strong></p>
    <div class="divider"></div>
    <p class="offer-lead">GET</p>
    <p class="offer-amount">20-60%</p>
    <p class="offer-tail">OFF</p>
  </section>
</body>
</html>
```